Real Estate Wordpress Landing Page

I'm looking to a landing page dedicated to my real estate brokerage that's catered to promoting that my company provides 1.5% listings to home sellers... I have a couple examples that I'm really looking towards mocking in a version with similar color schemes using my current company colors/website.

http://harbelo.com/
https://www.quarvantis.com/about/one-percent-listing-fee

My brokerage company website is http://www.brightmarrow.us/

Target Market(s)

real estate home sellers & buyers

Industry/Entity Type

Real Estate

Coding

Coded - Design and coding required

Number of Pages Required

1 page

Colors
3176b5
0255a3
eaf1f7
cedeed

Requirements
Must have
• Company website colors - http://www.brightmarrow.us/
• Something around the lines of this website page - http://harbelo.com/
• Wordpress compatibility

```html
<!DOCTYPE html>
<html lang="en">
<head>
<meta charset="utf-8">
<title>Bright Marrow – Real Estate Services</title>
<link rel="stylesheet" href="https://fonts.googleapis.com/css2?family=Roboto:wght@400;500;700;900&family=Open+Sans:wght@400;600;700&display=swap">
<style>
:root{
  --blue:#3176b5;
  --blue-deep:#0255a3;
  --blue-pale:#eaf1f7;
  --blue-soft:#cedeed;
  --ink:#222;
  --text:#555;
  --nav:#2a2c30;
  --dark:#15181d;
  --ribbon:#d12b2b;
  --white:#fff;
}
*{box-sizing:border-box;margin:0;padding:0}
html,body{width:1200px;height:2970px;overflow:hidden}
body{font-family:"Open Sans",Arial,sans-serif;color:var(--text);background:var(--white);position:relative}

/* header */
.site-header{position:absolute;left:0;top:0;width:1200px;height:115px;background:var(--white)}
.brand{position:absolute;left:122px;top:38px;display:flex;align-items:center;gap:12px;font-family:"Roboto",sans-serif;font-weight:700;font-size:24px;color:var(--blue-deep)}
.brand-mark{width:30px;height:30px;background:var(--blue-deep)}
.header-phone{position:absolute;right:114px;top:42px;display:flex;align-items:center;gap:12px;font-family:"Roboto",sans-serif;font-weight:500;font-size:27px;color:#333}
.main-nav{position:absolute;left:0;top:115px;width:1200px;height:60px;background:var(--nav);display:flex;align-items:center;justify-content:center;gap:38px;font-family:"Roboto",sans-serif;font-size:16px;color:var(--white);font-weight:500}
.main-nav .search{margin-left:8px}

/* hero */
.hero{position:absolute;left:0;top:175px;width:1200px;height:457px;
  background:
    radial-gradient(ellipse 120px 90px at 880px 215px,rgba(255,205,130,.55),transparent 70%),
    radial-gradient(ellipse 140px 100px at 300px 245px,rgba(255,195,120,.45),transparent 70%),
    radial-gradient(ellipse 260px 200px at 1120px 120px,rgba(20,28,22,.9),transparent 70%),
    linear-gradient(180deg,#6d8198 0%,#8d8a80 22%,#7e6f5c 45%,#4f4536 64%,#2f3a22 80%,#3c4d27 100%)}
.hero::after{content:"";position:absolute;inset:0;background:linear-gradient(90deg,rgba(0,0,0,.4),rgba(0,0,0,.05) 60%)}
.hero-copy{position:absolute;left:115px;top:82px;z-index:1;color:var(--white)}
.hero-kicker{font-family:"Roboto",sans-serif;font-weight:500;font-size:26px}
.hero-title{font-family:"Roboto",sans-serif;font-weight:700;font-size:62px;line-height:1.05;margin-top:6px}
.hero-sub{font-family:"Open Sans",sans-serif;font-weight:700;font-size:24px;line-height:1.35;width:660px;margin-top:8px}
.btn{display:inline-block;background:var(--blue);color:var(--white);font-family:"Open Sans",sans-serif;font-weight:700;text-transform:uppercase}
.hero .btn{margin-top:40px;font-size:19px;padding:13px 23px}
.slider-arrow{position:absolute;width:46px;height:46px;border:2px solid rgba(255,255,255,.8);border-radius:50%;display:flex;align-items:center;justify-content:center;z-index:1}

/* about */
.about-photo{position:absolute;left:117px;top:720px;width:503px;height:320px;
  background:
    radial-gradient(ellipse 160px 90px at 330px 200px,#3fa6e6,transparent 75%),
    radial-gradient(ellipse 150px 70px at 270px 60px,#d8e4ee,transparent 75%),
    linear-gradient(135deg,#0f2236 0%,#1f4f7a 40%,#2a86c4 60%,#1b4a36 85%,#0f2a1a 100%)}
.about-copy{position:absolute;left:673px;top:724px;width:412px}
.section-title{font-family:"Roboto",sans-serif;font-weight:700;color:var(--blue);font-size:32px;text-transform:uppercase}
.about-copy p{font-size:12px;line-height:2;color:#555;margin-top:20px}
.about-copy .btn{margin-top:26px;font-size:16px;padding:12px 20px}

/* stats */
.stats{position:absolute;left:0;top:1137px;width:1200px;height:463px;
  background:
    radial-gradient(ellipse 300px 160px at 200px 330px,rgba(120,115,110,.35),transparent 70%),
    radial-gradient(ellipse 260px 140px at 900px 120px,rgba(90,88,85,.35),transparent 70%),
    linear-gradient(180deg,#2c2c2d,#1c1d1f 60%,#111214);text-align:center;color:var(--white)}
.stats-head{position:absolute;left:0;top:88px;width:100%;font-family:"Roboto",sans-serif;font-weight:700;font-size:31px}
.stats-sub{position:absolute;left:0;top:132px;width:100%;font-family:"Roboto",sans-serif;font-weight:700;font-size:21px}
.stat{position:absolute;top:218px;text-align:center}
.stat-label{font-family:"Roboto",sans-serif;color:var(--blue);font-size:21px;text-transform:uppercase}
.stat-num{font-family:"Roboto",sans-serif;font-weight:700;font-size:48px;margin-top:10px}
.stat-rule{position:absolute;top:200px;width:2px;height:135px;background:var(--blue-deep)}
.dots{position:absolute;top:405px;left:0;width:100%;display:flex;justify-content:center;gap:3px}
.dots i{width:8px;height:8px;border:1.5px solid var(--white);border-radius:50%}
.dots i.on{background:var(--white)}

/* listings */
.listings-title{position:absolute;left:0;top:1680px;width:1200px;text-align:center}
.listings-intro{position:absolute;left:250px;top:1736px;width:700px;text-align:center;font-size:12.5px;line-height:2.1;color:#444}
.card{position:absolute;top:1818px;width:306px;height:400px;background:var(--white);border:1px solid #ddd;overflow:hidden;box-shadow:0 1px 3px rgba(0,0,0,.08)}
.card-photo{height:170px}
.ribbon{position:absolute;right:-38px;top:30px;width:170px;transform:rotate(45deg);background:var(--ribbon);color:var(--white);font-size:14px;text-align:center;padding:5px 0}
.card-plus{position:absolute;left:137px;top:152px;width:34px;height:34px;border-radius:50%;background:#2b2b2b;color:var(--white);font-size:22px;line-height:32px;text-align:center}
.card-body{padding:32px 13px 0}
.card-body h3{font-family:"Roboto",sans-serif;font-weight:700;color:var(--blue-deep);font-size:14px;text-transform:uppercase;white-space:nowrap}
.card-body ul{list-style:none;margin-top:10px;font-size:10.8px;line-height:2.15;color:#444;white-space:nowrap}
.card-foot{position:absolute;left:0;bottom:0;width:100%;height:80px;background:var(--blue-deep);color:var(--white);padding:18px 13px;font-size:12px;line-height:2.1}
.side-arrow{position:absolute;top:1975px;width:54px;height:54px;border-radius:50%;background:#f0f0f0;border:1px solid #ddd;display:flex;align-items:center;justify-content:center}

/* cta */
.cta{position:absolute;left:0;top:2310px;width:1200px;height:118px;background:linear-gradient(90deg,var(--blue-deep),#1565b0 50%,var(--blue-deep))}
.cta-text{position:absolute;left:117px;top:40px;color:var(--white);font-family:"Open Sans",sans-serif;font-weight:600;font-size:25px}
.cta-btn{position:absolute;left:886px;top:30px;width:200px;height:56px;background:var(--white);color:var(--blue-deep);font-family:"Roboto",sans-serif;font-weight:700;font-size:19px;display:flex;align-items:center;justify-content:center}

/* footer */
.site-footer{position:absolute;left:0;top:2428px;width:1200px;height:542px;background:linear-gradient(180deg,#1e2128,#121418)}
.footer-head{position:absolute;top:2520px;color:var(--white);font-family:"Roboto",sans-serif;font-weight:700;font-size:20px;text-transform:uppercase}
.field{position:absolute;left:120px;width:343px;height:40px;border:1px solid #bbb;color:var(--white);font-size:12px;padding:11px 8px}
.submit{position:absolute;left:120px;top:2806px;width:343px;height:40px;background:var(--blue-deep);color:var(--white);font-weight:700;font-size:13px;display:flex;align-items:center;justify-content:center}
.contact-row{position:absolute;left:518px;display:flex;gap:12px;color:var(--white);font-size:14px;line-height:1.6}
.ico{width:26px;height:26px;border:1.5px solid #ddd;border-radius:50%;flex:none;display:flex;align-items:center;justify-content:center}
.socials{position:absolute;left:518px;top:2738px;display:flex;gap:8px}
.socials i{width:24px;height:24px;border:1.5px solid #ddd;border-radius:50%}
.site-link{position:absolute;left:524px;top:2782px;color:var(--white);font-size:14px;text-decoration:underline}
.map{position:absolute;left:767px;top:2522px;width:318px;height:323px;
  background:
    radial-gradient(ellipse 90px 60px at 80px 260px,#cfe0c8,transparent 75%),
    radial-gradient(ellipse 80px 60px at 250px 70px,#d6dde6,transparent 75%),
    linear-gradient(135deg,#eceee9,#e1e5de);border:2px solid #ccc}
.copyright{position:absolute;left:0;top:2920px;width:1200px;text-align:center;color:var(--white);font-size:11px}
</style>
</head>
<body>

<header class="site-header">
  <div class="brand"><span class="brand-mark"></span>Bright Marrow</div>
  <div class="header-phone">
    <svg width="22" height="22" viewBox="0 0 24 24"><path fill="#0255a3" d="M6.6 10.8a15 15 0 0 0 6.6 6.6l2.2-2.2c.3-.3.7-.4 1-.2 1.1.4 2.3.6 3.6.6.6 0 1 .4 1 1V20c0 .6-.4 1-1 1A17 17 0 0 1 3 4c0-.6.4-1 1-1h3.5c.6 0 1 .4 1 1 0 1.3.2 2.5.6 3.6.1.3 0 .7-.2 1z"/></svg>
    +1 555-014-2276
  </div>
</header>

<nav class="main-nav">
  <span>HOME</span><span>ABOUT US</span><span>PROPERTY FOR SALE</span><span>CONSULTATION</span><span>BLOG</span><span>CONTACT US</span>
  <svg class="search" width="16" height="16" viewBox="0 0 16 16"><circle cx="6.5" cy="6.5" r="4.8" fill="none" stroke="#fff" stroke-width="2"/><path d="M10 10l4.5 4.5" stroke="#fff" stroke-width="2.4"/></svg>
</nav>

<section class="hero" role="img" aria-label="Photograph of a large stone-front luxury home at dusk with landscaped garden">
  <div class="hero-copy">
    <div class="hero-kicker">Real Estate Services</div>
    <h1 class="hero-title">BRIGHT MARROW</h1>
    <p class="hero-sub">Sed ut perspiciatis unde omnis iste natus arror sit voluptatem accusantium doloremque.</p>
    <span class="btn">Read More</span>
  </div>
  <div class="slider-arrow" style="left:43px;top:192px"><svg width="12" height="14" viewBox="0 0 12 14"><path d="M8 2L3 7l5 5" fill="none" stroke="#fff" stroke-width="2"/></svg></div>
  <div class="slider-arrow" style="left:1111px;top:192px"><svg width="12" height="14" viewBox="0 0 12 14"><path d="M4 2l5 5-5 5" fill="none" stroke="#fff" stroke-width="2"/></svg></div>
</section>

<section class="about">
  <div class="about-photo" role="img" aria-label="Aerial night view of a modern house with a lit swimming pool"></div>
  <div class="about-copy">
    <h2 class="section-title">About&nbsp; Bright Marrow</h2>
    <p>Sed ut perspiciatis unde omnis iste natus error sit voluptatem accusantium doloremque laudantium, totam rem aperiam, eaque ipsa quae ab illo inven tore veritatis et quasi architecto beatae vitae dicta sunt explicabo. Nemo enim ipsam voluptatem quia voluptas sit aspernatur aut odit aut fugit, sed quia consequuntur magni dolores eos qui ratione voluptatem sequi nesciunt. Neque porro quisquam est, qui dolorem ipsum quia dolor.</p>
    <span class="btn">Read More</span>
  </div>
</section>

<section class="stats" role="img" aria-label="Dimly lit living room interior background">
  <div class="stats-head">LIST FOR 1.5% COMMISSION,</div>
  <div class="stats-sub">AND RECEIVE TOP MARKETING FROM REAL ESTATE PRO!</div>
  <div class="stat" style="left:130px;width:150px"><div class="stat-label">Clients</div><div class="stat-num">2516</div></div>
  <div class="stat-rule" style="left:331px"></div>
  <div class="stat" style="left:380px;width:160px"><div class="stat-label">Projects</div><div class="stat-num">2860</div></div>
  <div class="stat-rule" style="left:594px"></div>
  <div class="stat" style="left:620px;width:225px"><div class="stat-label">Positive Reviews</div><div class="stat-num">3200</div></div>
  <div class="stat-rule" style="left:871px"></div>
  <div class="stat" style="left:895px;width:160px"><div class="stat-label">Employees</div><div class="stat-num">1320</div></div>
  <div class="dots"><i class="on"></i><i></i><i></i><i></i></div>
</section>

<h2 class="section-title listings-title">Property for Sale</h2>
<p class="listings-intro">Sed ut perspiciatis unde omnis iste natus error sit voluptatem accusantium doloremque laudantium, totam rem aperiam, eaque ipsa quae ab illo inventore veritatis et quasi architecto beatae vitae dicta sunt explicabo nemo enim ipsam quia voluptas sit aspernatur au.</p>

<div class="side-arrow" style="left:27px"><svg width="10" height="14" viewBox="0 0 10 14"><path d="M7 2L2 7l5 5" fill="none" stroke="#999" stroke-width="1.6"/></svg></div>
<div class="side-arrow" style="left:1125px"><svg width="10" height="14" viewBox="0 0 10 14"><path d="M3 2l5 5-5 5" fill="none" stroke="#999" stroke-width="1.6"/></svg></div>

<article class="card" style="left:117px">
  <div class="card-photo" role="img" aria-label="Two-storey white family home with garage" style="background:linear-gradient(180deg,#7fa9d6 0%,#b9cde0 25%,#e6e4dc 45%,#cfcac0 62%,#6f8f45 80%,#4d6f2c 100%)"></div>
  <div class="ribbon">saved $4,650</div>
  <div class="card-plus">+</div>
  <div class="card-body">
    <h3>Sell with Bright Marrow &amp; Save $$$</h3>
    <ul><li>Professional Real Estate Photography</li><li>Complimentary Comparative Market Analysis (CMA)</li><li>FREE Consultation with Real Estate Professional</li></ul>
  </div>
  <div class="card-foot">4812 Willowmere Lane<br>Cedar Bay, FL 33401 - $310,000</div>
</article>

<article class="card" style="left:448px">
  <div class="card-photo" role="img" aria-label="Bright living room with grey sofa and ceiling fan" style="background:linear-gradient(180deg,#efefed 0%,#d6d5d2 35%,#8f8d88 60%,#c9c7c2 78%,#5e5c58 100%)"></div>
  <div class="ribbon">saved $7,485</div>
  <div class="card-plus">+</div>
  <div class="card-body">
    <h3>Start your home search with us</h3>
    <ul><li>1% Buyer Credit at Closing from Bright Marrow</li><li>Quis Molestie Turpis Dapibus At</li><li>Quis Molestie Turpis Dapibus At</li></ul>
  </div>
  <div class="card-foot">718 Sandpiper Court, 104<br>Palm Cove, FL 33490 - $499,000</div>
</article>

<article class="card" style="left:779px">
  <div class="card-photo" role="img" aria-label="Beige two-storey house with palm trees" style="background:linear-gradient(180deg,#5f95d2 0%,#a9c4e2 25%,#e2d6bc 45%,#cbb995 62%,#6e8a46 80%,#4f6c2e 100%)"></div>
  <div class="ribbon">saved $4,650</div>
  <div class="card-plus">+</div>
  <div class="card-body">
    <h3>Leasing &amp; Property Management</h3>
    <ul><li>We can manage your rental portfolio for you!</li><li>Professional &amp; Experienced Property Managers</li><li>Receive Top Dollar for your Rental Properties</li></ul>
  </div>
  <div class="card-foot">9320 Amberfield Circle<br>Cedar Bay, FL 33412 - $310,000</div>
</article>

<section class="cta">
  <div class="cta-text">Get Started with Bright Marrow, Schedule a free Consultation!</div>
  <div class="cta-btn">SCHEDULE NOW</div>
</section>

<footer class="site-footer"></footer>
<div class="footer-head" style="left:120px">Let's Get in Touch</div>
<div class="field" style="top:2563px">Full Name</div>
<div class="field" style="top:2611px">Email Address</div>
<div class="field" style="top:2660px">Phone Number</div>
<div class="field" style="top:2710px;height:84px">Message</div>
<div class="submit">SUBMIT</div>

<div class="footer-head" style="left:518px">Contact</div>
<div class="contact-row" style="top:2560px"><span class="ico"><svg width="12" height="12" viewBox="0 0 24 24"><path fill="#fff" d="M6.6 10.8a15 15 0 0 0 6.6 6.6l2.2-2.2c.3-.3.7-.4 1-.2 1.1.4 2.3.6 3.6.6.6 0 1 .4 1 1V20c0 .6-.4 1-1 1A17 17 0 0 1 3 4c0-.6.4-1 1-1h3.5c.6 0 1 .4 1 1 0 1.3.2 2.5.6 3.6.1.3 0 .7-.2 1z"/></svg></span><span style="padding-top:2px">+1 555-014-2276</span></div>
<div class="contact-row" style="top:2604px"><span class="ico"><svg width="12" height="10" viewBox="0 0 12 10"><rect x=".5" y=".5" width="11" height="9" fill="none" stroke="#fff"/><path d="M.5.5L6 5.5 11.5.5" fill="none" stroke="#fff"/></svg></span><span style="padding-top:2px">info@brightmarrow.com</span></div>
<div class="contact-row" style="top:2650px"><span class="ico"><svg width="10" height="13" viewBox="0 0 10 13"><path d="M5 12.5S1 7.6 1 4.8a4 4 0 0 1 8 0C9 7.6 5 12.5 5 12.5z" fill="#fff"/><circle cx="5" cy="4.8" r="1.5" fill="#15181d"/></svg></span><span>2400 Harbor Crest Blvd,<br>Ste 310 Palm Cove,<br>Florida - 33490.</span></div>
<div class="socials"><i></i><i></i><i></i><i></i><i></i><i></i></div>
<div class="site-link">brightmarrow.us</div>
<div class="map" role="img" aria-label="Street map showing the office location"></div>
<div class="copyright">Copyright © 2018 . All Rights Reserved.</div>

</body>
</html>
```